Business card for marketing analytics company

Need a business card for new company. I have a logo already that I want to be built into the card and should use those colours

Company is called steered by tallies
Design must bring steered by tallies to life not be a card that could be for anyone with a logo put on it.

Like the front to be fairly clean and uncluttered bringing the logo out with a suitable design on the back of the card.

The logo represents a compass and business growth so those themes along with numbers, analytics , data are appropriate.
I'm often working with creative industries so also needs to reflect the creative side of analytics rather than be very corporate looking.

Target Market(s)

Ad agency, media agency, consumer goods clients

Industry/Entity Type

Market Research

Contact Information for Business Card

Needs to include name, title, email and phone number

Colors
f78f20
f68d4d
ec1f27

Requirements
Must have
• Must bring steered by tallies to life not be a card that could be for anyone with a logo put on it.
• Logo, Correct colours
• Like a design on the back that relates to company name
• Designs for both sides
Should not have
• Please do not just submit logo and a coloured card.
• It needs to have a design element to it
• No black background
• No clear cards - needs front & back

```html
<!DOCTYPE html>
<html lang="en">
<head>
<meta charset="utf-8">
<title>Steered by Tallies – Business Card</title>
<link rel="stylesheet" href="https://fonts.googleapis.com/css2?family=Figtree:wght@400;500;600&display=swap">
<style>
  :root {
    --page-bg: #2b2b2b;
    --card-white: #ffffff;
    --brand-orange: #f47427;
    --brand-red: #c01f25;
    --line-red: #c4202a;
    --text-white: #ffffff;
    --chart-tint: rgba(255, 255, 255, 0.13);
    --grid-tint: rgba(255, 255, 255, 0.08);
  }
  * { box-sizing: border-box; margin: 0; padding: 0; }
  html, body {
    width: 1200px;
    height: 987px;
    overflow: hidden;
    background: var(--page-bg);
    font-family: "Figtree", "Helvetica Neue", Arial, sans-serif;
  }
  .card {
    position: absolute;
    left: 293px;
    width: 615px;
    height: 352px;
    overflow: hidden;
  }
  .card--front { top: 130px; background: var(--card-white); }
  .card--back  { top: 505px; background: var(--brand-red); }

  .front-angle,
  .back-chart {
    position: absolute;
    inset: 0;
    width: 100%;
    height: 100%;
  }

  .brand {
    position: absolute;
    display: flex;
    align-items: center;
  }
  .brand__dot {
    border-radius: 50%;
    border: 3px solid currentColor;
    flex: none;
  }
  .brand__name {
    font-weight: 500;
    line-height: 1.0;
    text-align: right;
  }
  .card--front .brand { left: 36px; top: 36px; gap: 20px; color: var(--brand-orange); }
  .card--front .brand__dot { width: 95px; height: 95px; }
  .card--front .brand__name { font-size: 31px; }

  .contact {
    position: absolute;
    right: 34px;
    top: 188px;
    text-align: right;
    color: var(--text-white);
  }
  .contact__name { font-size: 21px; font-weight: 600; line-height: 1.2; }
  .contact__title { font-size: 17px; font-weight: 400; margin-bottom: 18px; }
  .contact__list { list-style: none; }
  .contact__item {
    display: flex;
    justify-content: flex-end;
    align-items: center;
    gap: 6px;
    font-size: 15px;
    line-height: 23.5px;
  }
  .contact__item:first-child { font-size: 16px; }
  .contact__icon { width: 16px; height: 16px; fill: var(--text-white); flex: none; }

  .card--back .brand {
    left: 126px;
    top: 119px;
    gap: 22px;
    color: var(--text-white);
  }
  .card--back .brand__dot { width: 111px; height: 111px; }
  .card--back .brand__name { font-size: 35px; }

  .back-url {
    position: absolute;
    left: 0;
    right: 0;
    top: 292px;
    text-align: center;
    color: var(--text-white);
    font-size: 15px;
    letter-spacing: 0.55em;
    padding-left: 0.55em;
  }
</style>
</head>
<body>

<section class="card card--front" aria-label="Card front">
  <svg class="front-angle" viewBox="0 0 615 352" preserveAspectRatio="none" aria-hidden="true">
    <polygon points="443,0 615,0 615,352 282,352" fill="var(--brand-orange)"/>
    <line x1="438" y1="0" x2="277" y2="352" stroke="var(--line-red)" stroke-width="2.5"/>
  </svg>

  <div class="brand">
    <span class="brand__dot"></span>
    <p class="brand__name">Steered by<br>Tallies</p>
  </div>

  <div class="contact">
    <p class="contact__name">Mara Quill</p>
    <p class="contact__title">President</p>
    <ul class="contact__list">
      <li class="contact__item">555 0142 7789
        <svg class="contact__icon" viewBox="0 0 16 16" aria-hidden="true">
          <path d="M2 5c0-2 2.5-3 6-3s6 1 6 3v1.5h-3V5H5v1.5H2z"/>
          <path d="M4 7h8l2 6H2z"/>
        </svg>
      </li>
      <li class="contact__item">mara@steeredbytally.com
        <svg class="contact__icon" viewBox="0 0 16 16" aria-hidden="true">
          <path d="M1 3h14v1.2L8 9 1 4.2z"/>
          <path d="M1 5.6 8 10.4l7-4.8V13H1z"/>
        </svg>
      </li>
      <li class="contact__item">www.steeredbytally.com
        <svg class="contact__icon" viewBox="0 0 16 16" aria-hidden="true">
          <circle cx="8" cy="8" r="7"/>
          <path d="M5 4c1.5 0 2 1 1.5 2S4 7 5 9s2.5 1 2.5 3M10 3.5c-.5 1.5.5 2 1.5 2.5s1 2-.5 3" stroke="var(--brand-orange)" stroke-width="1.3" fill="none"/>
        </svg>
      </li>
    </ul>
  </div>
</section>

<section class="card card--back" aria-label="Card back">
  <svg class="back-chart" viewBox="0 0 615 352" aria-hidden="true">
    <g stroke="var(--grid-tint)" stroke-width="1">
      <line x1="0" y1="60" x2="615" y2="60"/>
      <line x1="0" y1="100" x2="615" y2="100"/>
      <line x1="0" y1="260" x2="615" y2="260"/>
      <line x1="0" y1="330" x2="615" y2="330"/>
    </g>
    <g fill="var(--chart-tint)">
      <rect x="515" y="300" width="14" height="52"/>
      <rect x="535" y="272" width="14" height="80"/>
      <rect x="555" y="240" width="14" height="112"/>
      <rect x="575" y="200" width="14" height="152"/>
      <rect x="595" y="152" width="14" height="200"/>
      <rect x="14"  y="322" width="14" height="30"/>
      <rect x="34"  y="308" width="14" height="44"/>
      <rect x="54"  y="316" width="14" height="36"/>
    </g>
  </svg>

  <div class="brand">
    <span class="brand__dot"></span>
    <p class="brand__name">Steered by<br>Tallies</p>
  </div>
  <p class="back-url">www.steeredbytally.com</p>
</section>

</body>
</html>
```